Hop Along Days campaign: promoting kids play in the UK - Website Redesign

Hop Along Days is a national UK campaign that promotes the value of play for children. The current website is live at http://www.hopalongdays.co.uk. This website has been live for 4 years and now needs to be redesigned. The target audience is parents of young children up to the age of 12.

The current site was designed with a series of old adverts in mind. Here is an example of an old advert: http://vidshare.example/qR7tLm2XwZa

Criticisms of existing site:
The design represented the adverts too closely. The result was a website that mirrors the adverts rather than complements them.
The color scheme is too dark.
Text-heavy pages (e.g. http://www.hopalongdays.co.uk/fun.php) are dull and not FUN!

New site
We have recently had a series of new video adverts produced:
advert 1: http://vidshare.example/hB4nVc8JsPe
advert 2: http://vidshare.example/KgW3rTy9DuM
advert 3: http://vidshare.example/zA5oEi1HbNq

The new site should be cleaner and brighter than the existing site, possibly with a white background using graphics, fonts and advert characters (see attached character graphics files) to add the element of fun and play.

The homepage should include:
1. Hop Along Days logo (attached)
2. Social Media links (visible on all pages of the site) – Chatterbook, Chirpline, ClipVault
3. Link to the HopAlongDays app page of the site (visible on all pages)
4. Image/video placeholder that the user can scroll through, view full-size images and play videos.
5. Text area to hold approximately 100 words describing the purpose of the campaign
6. Site footer to contain the same information as on the existing site along with the Northern Games & Crafts Guild logo (attached)

Site structure:
One change to the site structure… the “Brought to you by” menu item will be removed from the top-level menu.

General:
Some pages on the existing site are quite text-heavy, we would like to break up text on these pages in some way. Graphical division of paragraphs, use of advert characters?

Please note that all attached graphics file are the property of the Northern Games & Crafts Guild and must only be used for the purpose of this project.

```html
<!DOCTYPE html>
<html lang="en">
<head>
<meta charset="utf-8">
<title>Hop Along Days – Home</title>
<link rel="stylesheet" href="https://fonts.googleapis.com/css2?family=Arimo:wght@400;700&family=Montserrat:wght@800;900&family=PT+Sans:wght@400;700&display=swap">
<style>
:root{
  --backdrop:#d6d6d6;
  --page:#ffffff;
  --hero:#2aa9d0;
  --title:#f6e23a;
  --nav-orange:#e9b32f;
  --nav-purple:#5a3e8f;
  --nav-sky:#5ab4e5;
  --nav-yellow:#e6c81f;
  --nav-pink:#d4557a;
  --app-green:#b9d04a;
  --app-edge:#93a935;
  --cta-pink:#e0457a;
  --ink:#333333;
  --heading:#555555;
  --rule:#cfcfcf;
  --accent:#3fb3d6;
  --accent-dark:#2f5fbf;
  --muted:#9a9a9a;
  --views:#c0202a;
  --thumb-edge:#9aacb3;
}
*{box-sizing:border-box;margin:0;padding:0}
html,body{width:1200px;height:1089px;overflow:hidden;background:var(--backdrop)}
.stage{position:relative;width:1400px;height:1270px;transform:scale(0.857143);transform-origin:0 0;font-family:"PT Sans",sans-serif;color:var(--ink)}
.page{position:absolute;left:200px;top:0;width:1000px;height:1270px;background:var(--page)}
.abs{position:absolute}

.social{position:absolute;top:16px;left:1095px;display:flex;gap:7px}
.social a{width:22px;height:22px;border-radius:50%;background:var(--accent-dark);display:block}
.social a:nth-child(2){background:var(--accent)}
.social a:nth-child(3){background:var(--nav-sky)}

.brand{left:268px;top:52px;font-family:"PT Sans",sans-serif;font-weight:700;font-size:20px;color:var(--nav-purple)}

.main-nav{position:absolute;left:553px;top:52px;display:flex}
.main-nav a{width:130px;height:45px;display:flex;align-items:center;justify-content:center;color:#fff;font:700 14px "Arimo",sans-serif;text-decoration:none;border-right:1px solid #fff}
.main-nav a:last-child{border-right:0}

.hero{position:absolute;left:200px;top:98px;width:1000px;height:302px;background:var(--hero)}
.video-frame{position:absolute;left:272px;top:111px;width:500px;height:270px;background:#fff;padding:6px}
.video-art{width:100%;height:100%;background:linear-gradient(135deg,#9bb04a,#e9e4d6 50%,#6f9a3a)}
.play-btn{position:absolute;left:494px;top:220px;width:60px;height:54px;border-radius:8px;background:rgba(220,220,220,.8)}
.hero-title{left:820px;top:138px;font:900 46px/56px "Montserrat",sans-serif;color:var(--title)}
.hero-copy{left:820px;top:266px;width:345px;font:700 10px/22px "Arimo",sans-serif;color:#fff}

.carousel-arrow{top:455px}
.thumb{top:424px;width:140px;height:83px;border:3px solid var(--thumb-edge)}
.thumb .art{width:100%;height:100%}

.app-box{left:824px;top:416px;width:293px;height:122px;background:var(--app-green);border:1px solid var(--app-edge);border-radius:3px}
.app-title{left:940px;top:433px;width:150px;text-align:center;font:700 25px/28px "Arimo",sans-serif;color:#fff}
.app-cta{left:944px;top:503px;width:136px;height:26px;background:var(--cta-pink);border-radius:3px;color:#fff;font:700 17px/26px "Arimo",sans-serif;text-align:center}

.welcome-title{left:233px;top:552px;font:700 20px "Arimo",sans-serif;color:var(--heading)}
.welcome-rule{left:233px;top:592px;width:930px;height:1px;background:var(--rule)}
.welcome-copy{left:233px;top:615px;width:924px;font-size:11.4px;line-height:20px;text-align:justify}

.feed-title{top:776px;font-size:21px;color:var(--ink);white-space:nowrap}
.feed-title span{color:var(--accent)}
.feed-dots{top:791px;height:5px;border-top:1px dotted #bbb;border-bottom:1px dotted #bbb}
.feed-item{position:absolute;width:280px;height:70px}
.feed-item .pic{position:absolute;left:0;top:0;width:60px;height:55px;border:1px solid #ccc}
.feed-item p{position:absolute;left:76px;top:0;width:200px;font-size:12px;line-height:16px}
.feed-item .meta{position:absolute;left:76px;top:54px;width:180px;font-size:10px;color:var(--accent);display:flex;justify-content:space-between}
.feed-item .views{color:var(--views)}
.btn-more{top:1082px;width:65px;height:12px;font:400 10px/12px "Arimo",sans-serif;color:#fff;text-align:center}

.footer-rule{left:222px;top:1153px;width:936px;height:1px;background:#999}
.partner{left:262px;top:1196px;width:110px;font:700 13px/16px "PT Sans",sans-serif;color:var(--ink);text-align:center}
.footer-links{left:440px;top:1181px;width:640px;text-align:center;font:700 12px/24px "Arimo",sans-serif;color:var(--muted);word-spacing:2px}
.footer-links .sep{margin:0 18px}
.copyright{left:440px;top:1228px;width:640px;text-align:center;font:700 12px "Arimo",sans-serif;color:var(--muted)}
</style>
</head>
<body>
<div class="stage">
  <div class="page"></div>

  <nav class="social" aria-label="Social links">
    <a href="#" aria-label="Chatterbook"></a>
    <a href="#" aria-label="Chirpline"></a>
    <a href="#" aria-label="ClipVault"></a>
  </nav>

  <div class="abs brand">Hop Along Days</div>

  <nav class="main-nav">
    <a href="#" style="background:var(--nav-orange)">Play Right Now</a>
    <a href="#" style="background:var(--nav-purple)">Get Involved</a>
    <a href="#" style="background:var(--nav-sky)">WhyPlay</a>
    <a href="#" style="background:var(--nav-yellow)">Fun Forever</a>
    <a href="#" style="background:var(--nav-pink)">Resourcrs</a>
  </nav>

  <section class="hero"></section>
  <div class="video-frame"><div class="video-art" role="img" aria-label="Advert still: cartoon children beside a signpost in a leafy park"></div></div>
  <div class="play-btn"><svg width="60" height="54" viewBox="0 0 60 54"><path d="M24 17 L38 27 L24 37 Z" fill="#222"/></svg></div>
  <h1 class="abs hero-title">HOP ALONG<br>DAYS</h1>
  <p class="abs hero-copy">Hop Along Days Ambassador Dr Mara Linwood explains the importance of engaging children in physical activity and the body image rock out her blog link</p>

  <svg class="abs carousel-arrow" style="left:272px" width="18" height="20" viewBox="0 0 18 20"><path d="M14 2 L5 10 L14 18" stroke="var(--hero)" stroke-width="4" fill="none"/></svg>
  <div class="abs thumb" style="left:297px"><div class="art" role="img" aria-label="Advert still: campaign sign" style="background:linear-gradient(#f3efe6,#d9cfc0)"></div></div>
  <div class="abs thumb" style="left:447px"><div class="art" role="img" aria-label="Advert still: cartoon girl in a park" style="background:linear-gradient(135deg,#8fa84a,#e46a7a)"></div></div>
  <div class="abs thumb" style="left:597px"><div class="art" role="img" aria-label="Advert still: children around a signpost" style="background:linear-gradient(135deg,#7fa04a,#efe8dc 55%,#4a6fbf)"></div></div>
  <svg class="abs carousel-arrow" style="left:746px" width="18" height="20" viewBox="0 0 18 20"><path d="M4 2 L13 10 L4 18" stroke="var(--hero)" stroke-width="4" fill="none"/></svg>

  <div class="abs app-box"></div>
  <svg class="abs" style="left:860px;top:421px" width="56" height="113" viewBox="0 0 56 113">
    <rect x="1" y="1" width="54" height="111" rx="9" fill="#1d1d1d"/>
    <rect x="6" y="16" width="44" height="78" fill="#fff"/>
    <circle cx="28" cy="103" r="4" fill="none" stroke="#666" stroke-width="1.5"/>
    <text x="28" y="85" font-family="Arimo,sans-serif" font-size="8" font-weight="700" text-anchor="middle" fill="#333">START</text>
  </svg>
  <div class="abs app-title">APP<br>AVAILABLE</div>
  <a href="#" class="abs app-cta">CLICK HERE</a>

  <h2 class="abs welcome-title">WELCOME</h2>
  <div class="abs welcome-rule"></div>
  <p class="abs welcome-copy">Maecenas ipsum metus, semper hendrerit varius mattis, congue sit amet tellus. Aliquam ullamcorper dui sed magna posue re ut elementum enim rutrum. Nam mi erat, porta id ultrices nec, pellentesque vel nunc. Cras varius fermentum iaculis. Aenean sodales nibh non lectus tempor a interdum justo ultricies.Maecenas ipsum metus, semper hendrerit varius mattis, congue sit amet tellus. Aliquam ullamcorper dui sed magna posue re ut elementum enim rutrum. Nam mi erat, porta id ultrices nec, pellentesque vel nunc. Cras varius fermentum iaculis. Aenean sodales nibh non lectus tempor a interdum justo ultricies.Maecenas ipsum metus, semper hendrerit varius mattis, congue sit amet tellus. Aliquam ullamcorper dui sed magna posue re ut elementum enim rutrum. Nam mi erat, porta id ultrices nec, pellentesque vel nunc. Cras varius fermentum iaculis. Aenean sodales nibh non lectus tempor a interdum justo ultricies Nam mi erat, porta id ultrices nec, pellentesque.</p>

  <!-- Chirpline column -->
  <h3 class="abs feed-title" style="left:220px">Chirpline <span>Feeds</span></h3>
  <div class="abs feed-dots" style="left:372px;width:120px"></div>
  <div class="feed-item" style="left:223px;top:827px"><div class="pic" role="img" aria-label="Member profile photo" style="background:#8a6a4a"></div><p>Donec luctus nisl in nibh ultricies quis convallis justo convallis. Fusce mattis mauris id enim.</p><div class="meta"><span>2-days ago</span><span>mery/</span></div></div>
  <div class="feed-item" style="left:223px;top:911px"><div class="pic" role="img" aria-label="Member profile photo" style="background:#c89a6a"></div><p>Donec luctus nisl in nibh ultricies quis convallis justo convallis. Fusce mattis mauris id enim.</p><div class="meta"><span>2-days ago</span><span>mery/</span></div></div>
  <div class="feed-item" style="left:223px;top:995px"><div class="pic" role="img" aria-label="Stage event photo" style="background:linear-gradient(#e0601a,#3a1a2a)"></div><p>Donec luctus nisl in nibh ultricies quis convallis justo convallis. Fusce mattis mauris id enim.</p><div class="meta"><span>2-days ago</span><span>mery/</span></div></div>
  <a href="#" class="abs btn-more" style="left:414px;background:var(--accent)">Read More</a>

  <!-- Chatterbook column -->
  <h3 class="abs feed-title" style="left:555px">Chatterbook <span style="color:var(--accent-dark)">Feeds</span></h3>
  <div class="abs feed-dots" style="left:750px;width:78px"></div>
  <div class="feed-item" style="left:558px;top:827px"><div class="pic" role="img" aria-label="Member profile photo" style="background:#8a6a4a"></div><p>Donec luctus nisl in nibh ultricies quis convallis justo convallis. Fusce mattis mauris id enim.</p><div class="meta"><span>2-days ago</span></div></div>
  <div class="feed-item" style="left:558px;top:911px"><div class="pic" role="img" aria-label="Member profile photo" style="background:#c89a6a"></div><p>Donec luctus nisl in nibh ultricies quis convallis justo convallis. Fusce mattis mauris id enim.</p><div class="meta"><span>2-days ago</span></div></div>
  <div class="feed-item" style="left:558px;top:995px"><div class="pic" role="img" aria-label="Stage event photo" style="background:linear-gradient(#e0601a,#3a1a2a)"></div><p>Donec luctus nisl in nibh ultricies quis convallis justo convallis. Fusce mattis mauris id enim.</p><div class="meta"><span>2-days ago</span></div></div>
  <a href="#" class="abs btn-more" style="left:749px;background:var(--accent-dark)">Read More</a>

  <!-- ClipVault column -->
  <h3 class="abs feed-title" style="left:886px">ClipVault</h3>
  <div class="abs feed-dots" style="left:1024px;width:134px"></div>
  <div class="feed-item" style="left:889px;top:827px"><div class="pic" role="img" aria-label="Advert video still" style="width:100px;background:linear-gradient(135deg,#7fa04a,#efe8dc 55%,#e46a7a)"></div><p style="left:119px;width:150px">Donec luctus nisl in nibh ultricies quis convallis justo</p><div class="meta" style="left:119px;top:42px"><span class="views">1200/ vies</span></div></div>
  <div class="feed-item" style="left:889px;top:915px"><div class="pic" role="img" aria-label="Advert video still" style="width:100px;background:linear-gradient(135deg,#7fa04a,#efe8dc 55%,#e46a7a)"></div><p style="left:119px;width:150px">Donec luctus nisl in nibh ultricies quis convallis justo</p><div class="meta" style="left:119px;top:42px"><span class="views">1200/ vies</span></div></div>
  <div class="feed-item" style="left:889px;top:997px"><div class="pic" role="img" aria-label="Advert video still" style="width:100px;background:linear-gradient(135deg,#7fa04a,#efe8dc 55%,#e46a7a)"></div><p style="left:119px;width:150px">Donec luctus nisl in nibh ultricies quis convallis justo</p><div class="meta" style="left:119px;top:42px"><span class="views">1200/ vies</span></div></div>
  <a href="#" class="abs btn-more" style="left:1080px;background:var(--accent)">More videos</a>

  <footer>
    <div class="abs footer-rule"></div>
    <div class="abs partner">Northern Games &amp; Crafts Guild</div>
    <div class="abs footer-links">Play Right Now<span class="sep">|</span>Get Involved<span class="sep">|</span>WhyPlay<span class="sep">|</span>Fun Forever<span class="sep">|</span>Resourcrs<br>Privacy Policy &nbsp;| Terms</div>
    <div class="abs copyright">Copyright © 2014 hopalongdays.co.uk. All Rights Reserved.</div>
  </footer>
</div>
</body>
</html>
```